Brenlow Estates Website and Logo Design

We need a new logo and website designed for 'Brenlow Estates Ltd', which is a well established Guernsey property holding company founded in 1934.

The company does not currently have a website. The new website should be similar in style and layout to https://www.quorvanhall.example/.

Target Market(s)

Industry, Media, Tenants

Industry/Entity Type

Property Management

Logo Text

BEL OR Brenlow Estates Ltd OR BE

Coding

Coded - Design and coding required

Number of Pages Required

4 page

Font styles to use
Other font styles liked:
• Helvetica

Requirements
Must have
• The logo laying over the picture (like https://www.quorvanhall.example/).
• Big pictures on homepage (like https://www.quorvanhall.example/)

```html
<!DOCTYPE html>
<html lang="en">
<head>
<meta charset="utf-8">
<title>Brenlow Estates Ltd</title>
<link href="https://fonts.googleapis.com/css2?family=Open+Sans:wght@400;600&family=Great+Vibes&family=PT+Serif&display=swap" rel="stylesheet">
<style>
:root{
  --teal:#0e5a6e;
  --teal-dark:#0a4455;
  --green:#8cc63f;
  --green-text:#6ab43e;
  --ink:#333;
  --bar:#1b2a30;
  --grey:#e9ecec;
  --white:#fff;
}
*{margin:0;padding:0;box-sizing:border-box}
html,body{width:1200px;height:3429px;overflow:hidden}
body{position:relative;background:var(--white);font-family:"Open Sans",Helvetica,Arial,sans-serif;color:var(--ink)}
.abs{position:absolute}
.photo{position:absolute}

/* header */
.topbar{left:0;top:0;width:1200px;height:32px;background:var(--bar)}
.social-top{right:40px;top:5px;display:flex;gap:6px}
.social-top span{width:22px;height:22px;border:1px solid #566;display:block}
.logo-panel{left:0;top:0;width:540px;height:135px;background:var(--teal);clip-path:polygon(0 0,100% 0,88% 100%,0 100%)}
.logo{left:78px;top:20px;display:flex;align-items:center;gap:16px}
.logo-mark{width:86px;height:86px;border:3px solid var(--white);border-radius:50%}
.logo-name{color:var(--white);font-weight:600;font-size:34px;line-height:1.05;width:280px}
.nav{left:490px;top:32px;width:710px;height:64px;background:var(--green);clip-path:polygon(5% 0,100% 0,100% 100%,0 100%)}
.nav ul{list-style:none;display:flex;height:100%;align-items:center;padding-left:90px}
.nav li{color:var(--white);font-size:17px;width:125px;text-align:center}
.phone-row{left:470px;top:96px;width:730px;height:38px;background:var(--grey);clip-path:polygon(3% 0,100% 0,100% 100%,0 100%)}
.phone{right:85px;top:104px;font-size:17px;color:#444;display:flex;align-items:center;gap:10px}

/* hero */
.hero{left:0;top:133px;width:1200px;height:576px;background:linear-gradient(180deg,#7fb3e3 0%,#c9def0 40%,#6c7d87 62%,#4f7346 72%,#7d8f9c 100%)}
.hero-panel{left:571px;top:576px;width:629px;height:133px;background:var(--teal);clip-path:polygon(12% 0,100% 0,100% 100%,0 100%)}
.hero-tag{right:80px;top:600px;color:var(--white);font-family:"PT Serif",serif;font-style:italic;font-size:17px}
.hero-title{right:80px;top:622px;color:var(--white);font-family:"PT Serif",serif;font-size:56px;letter-spacing:1px}

/* shared type */
.label{font-family:"Great Vibes",cursive;font-size:22px;line-height:28px;color:var(--teal)}
.section-title{font-size:37px;line-height:44px;color:var(--green-text);font-weight:400}
.copy{font-size:15px;line-height:23px}
.on-dark{color:var(--white)}
.on-dark .label{color:var(--white)}
.on-dark .section-title{color:var(--white)}

.btn{display:flex;width:206px;height:44px;position:absolute}
.btn.inline{position:relative;margin-top:18px}
.btn-text{width:140px;background:var(--teal);color:var(--white);font-size:15px;display:flex;align-items:center;justify-content:center;clip-path:polygon(0 0,100% 0,88% 100%,0 100%)}
.btn-icon{width:80px;margin-left:-14px;background:var(--green);display:flex;align-items:center;justify-content:center;clip-path:polygon(18% 0,100% 0,100% 100%,0 100%)}
.btn.alt .btn-text{background:var(--green)}
.btn.alt .btn-icon{background:var(--white)}

/* welcome */
.welcome{left:0;top:709px;width:1200px;text-align:center}
.welcome-ring{left:490px;top:735px;width:220px;height:220px;border:22px solid #eef0f0;border-radius:50%}
.welcome .label{margin-top:50px}
.welcome .section-title{margin-top:-6px}
.welcome .copy{width:930px;margin:10px auto 0;color:#444}
.welcome .btn{margin:18px auto 0}

/* feature bands */
.band{left:0;width:1200px;height:343px;overflow:hidden}
.band-text{width:520px}
.band-text .section-title{margin-top:-4px;margin-bottom:14px}
</style>
</head>
<body>

<header>
  <div class="abs topbar"></div>
  <div class="abs social-top"><span></span><span></span><span></span><span></span><span></span><span></span></div>
  <div class="abs logo-panel"></div>
  <div class="abs logo"><div class="logo-mark"></div><div class="logo-name">Brenlow Estates Ltd</div></div>
  <nav class="abs nav"><ul><li>HOME</li><li>ABOUT</li><li>PROJECTS</li><li>NEWS</li><li>CONTACT</li></ul></nav>
  <div class="abs phone-row"></div>
  <div class="abs phone">
    <svg width="18" height="18" viewBox="0 0 24 24"><path d="M6.6 10.8a15 15 0 0 0 6.6 6.6l2.2-2.2c.3-.3.7-.4 1-.2 1.1.4 2.3.6 3.6.6.6 0 1 .4 1 1V20c0 .6-.4 1-1 1A17 17 0 0 1 3 4c0-.6.4-1 1-1h3.5c.6 0 1 .4 1 1 0 1.3.2 2.5.6 3.6.1.3 0 .7-.2 1z" fill="#0e5a6e"/></svg>
    555-014-2290
  </div>
</header>

<section>
  <div class="photo hero" role="img" aria-label="City skyline by the river under a blue sky with clouds"></div>
  <div class="abs hero-panel"></div>
  <div class="abs hero-tag">How innovation, not regulation, can improve public health</div>
  <div class="abs hero-title">REAL HOMES</div>
</section>

<section>
  <div class="abs welcome-ring"></div>
  <div class="abs welcome">
    <div class="label">Welcome to Our Site</div>
    <h1 class="section-title">Brenlow Estates Limited</h1>
    <p class="copy">Brenlow Estates Limited (BEL) is a family-owned Guernsey property holding company. It purchases properties that are considered to have potential for development either through refurbishment or by obtaining planning permission to change its classification from, for example, industrial premises to offices or retail outlets, or by the marriage value of buying an adjacent property to one already owned by BEL.</p>
    <div class="btn inline"><div class="btn-text">READ MORE</div><div class="btn-icon"><svg width="26" height="26" viewBox="0 0 26 26"><circle cx="13" cy="13" r="10" fill="none" stroke="#fff" stroke-width="2.5"/><path d="M11 8l5 5-5 5" fill="none" stroke="#fff" stroke-width="2.5"/></svg></div></div>
  </div>
</section>

<!-- Why Guernsey -->
<section class="abs band" style="top:1051px">
  <div class="photo" style="left:0;top:0;width:1200px;height:343px;background:linear-gradient(180deg,#123a6a 0%,#1d3f6e 55%,#c98a3a 80%,#3a3f52 100%)" role="img" aria-label="Waterfront towers lit up at dusk"></div>
  <div class="abs" style="left:0;top:0;width:690px;height:343px;background:var(--teal);opacity:.93;clip-path:polygon(0 0,100% 0,83% 100%,0 100%)"></div>
  <div class="abs band-text on-dark" style="left:80px;top:52px">
    <div class="label">Why Us?</div>
    <h2 class="section-title">Why Guernsey?</h2>
    <p class="copy">The Bailiwick of Guernsey is a British Crown dependency in the English Channel. The benefit of establishing a company in Guernsey is the island's low tax jurisdiction since there are no capital taxes and no corporation taxes for many companies.</p>
    <div class="btn alt inline"><div class="btn-text">READ MORE</div><div class="btn-icon"><svg width="26" height="26" viewBox="0 0 26 26"><circle cx="13" cy="13" r="10" fill="none" stroke="#0e5a6e" stroke-width="2.5"/><path d="M11 8l5 5-5 5" fill="none" stroke="#0e5a6e" stroke-width="2.5"/></svg></div></div>
  </div>
</section>

<!-- Yesterday -->
<section class="abs band" style="top:1394px">
  <div class="photo" style="left:0;top:0;width:1200px;height:343px;background:linear-gradient(90deg,#9a8a66 0%,#b7a57c 25%,#7c8f5a 45%,#dfe6ea 62%,#fff 80%)" role="img" aria-label="Two-storey apartment building with lawn and parked car"></div>
  <div class="abs band-text" style="left:612px;top:40px">
    <div class="label">What we do?</div>
    <h2 class="section-title">Yesterday</h2>
    <p class="copy" style="color:#222">BEL was founded in 1934 by Edmund Brenlow to manage both his own extensive investments and his property portfolio in Guernsey. His property portfolio consisted of twenty properties each valued at approximately £1,500 – which also included the fixtures, fittings and furniture.</p>
    <div class="btn inline"><div class="btn-text">READ MORE</div><div class="btn-icon"><svg width="26" height="26" viewBox="0 0 26 26"><circle cx="13" cy="13" r="10" fill="none" stroke="#fff" stroke-width="2.5"/><path d="M11 8l5 5-5 5" fill="none" stroke="#fff" stroke-width="2.5"/></svg></div></div>
  </div>
</section>

<!-- Today -->
<section class="abs band" style="top:1737px">
  <div class="photo" style="left:0;top:0;width:1200px;height:343px;background:linear-gradient(180deg,#cfe0ec 0%,#b8c2c6 40%,#5e7c8a 65%,#2e5668 100%)" role="img" aria-label="Harbour with moored boats and a hillside town"></div>
  <div class="abs" style="left:0;top:0;width:690px;height:343px;background:var(--teal);opacity:.93;clip-path:polygon(0 0,100% 0,83% 100%,0 100%)"></div>
  <div class="abs band-text on-dark" style="left:80px;top:40px">
    <div class="label">What we do?</div>
    <h2 class="section-title">Today</h2>
    <p class="copy">The Brenlow family has steadily built on the foundations set out by the founder and each generation develops and manages the company appropriate to the era. The pride of being a part of a family company has ensured that all the thirty-three shareholders participate in its development.</p>
    <div class="btn alt inline"><div class="btn-text">READ MORE</div><div class="btn-icon"><svg width="26" height="26" viewBox="0 0 26 26"><circle cx="13" cy="13" r="10" fill="none" stroke="#0e5a6e" stroke-width="2.5"/><path d="M11 8l5 5-5 5" fill="none" stroke="#0e5a6e" stroke-width="2.5"/></svg></div></div>
  </div>
</section>

<!-- Tomorrow -->
<section class="abs band" style="top:2080px;height:348px">
  <div class="photo" style="left:0;top:0;width:1200px;height:348px;background:linear-gradient(90deg,#c9dbe0 0%,#dfe9ea 35%,#f2f6f6 60%,#fff 85%)" role="img" aria-label="Resort pool terrace lined with palm trees"></div>
  <div class="abs band-text" style="left:612px;top:40px">
    <div class="label">What we do?</div>
    <h2 class="section-title">Tomorrow</h2>
    <p class="copy" style="color:#222">In keeping with its past project development philosophy, its intrinsic understanding of the local property market and the successful management succession of the younger generation of the Brenlow family, the future in the Bailiwick of Guernsey is optimistic despite the economic fluctuations throughout much of Europe.</p>
    <div class="btn inline"><div class="btn-text">READ MORE</div><div class="btn-icon"><svg width="26" height="26" viewBox="0 0 26 26"><circle cx="13" cy="13" r="10" fill="none" stroke="#fff" stroke-width="2.5"/><path d="M11 8l5 5-5 5" fill="none" stroke="#fff" stroke-width="2.5"/></svg></div></div>
  </div>
</section>

<!-- Our Project -->
<section>
  <div class="abs" style="left:0;top:2475px;width:1200px;text-align:center">
    <div class="label">Our Work</div>
    <h2 class="section-title" style="margin-top:-8px">Our Project</h2>
  </div>
  <div class="photo" style="left:78px;top:2563px;width:253px;height:153px;background:linear-gradient(135deg,#d9d4cc,#8a8f96)" role="img" aria-label="Modern apartment living room"></div>
  <div class="photo" style="left:78px;top:2727px;width:253px;height:210px;background:linear-gradient(180deg,#c7d6df,#5f7a55 60%,#3c5a34)" role="img" aria-label="Residential tower above forest"></div>
  <div class="photo" style="left:341px;top:2563px;width:253px;height:231px;background:linear-gradient(180deg,#6aa2d8,#d9c79a 55%,#4d8a96)" role="img" aria-label="Beach villa with pool and palms"></div>
  <div class="photo" style="left:341px;top:2805px;width:253px;height:132px;background:linear-gradient(180deg,#e0c9a8,#b26d3a)" role="img" aria-label="Terrace with flowers at sunset"></div>
  <div class="photo" style="left:604px;top:2563px;width:255px;height:137px;background:linear-gradient(180deg,#a9c6df,#8d8f88 50%,#4d6d80)" role="img" aria-label="Harbour town with boats"></div>
  <div class="photo" style="left:604px;top:2709px;width:255px;height:228px;background:linear-gradient(180deg,#8fb8dc,#c7ccd0 50%,#5e879c)" role="img" aria-label="Waterfront apartment complex"></div>
  <div class="photo" style="left:869px;top:2563px;width:253px;height:205px;background:linear-gradient(180deg,#3d7fc0,#a9875a 60%,#5a4a36)" role="img" aria-label="Stone castle on a rocky coast"></div>
  <div class="photo" style="left:869px;top:2778px;width:253px;height:159px;background:linear-gradient(180deg,#8ec3ea,#d8c7a8 50%,#2c9fc4)" role="img" aria-label="Villa with round swimming pool"></div>
</section>

<!-- Contact -->
<section>
  <div class="photo" style="left:709px;top:2980px;width:491px;height:385px;background:linear-gradient(90deg,rgba(255,255,255,1) 0%,#dfe4e8 35%,#b9c3cb 70%,#a7b2bc 100%)" role="img" aria-label="Business team in office attire"></div>
  <div class="abs" style="left:0;top:2990px;width:1200px;text-align:center">
    <div class="label">Get in Touch with Us</div>
    <h2 class="section-title" style="margin-top:-8px">Contact Us</h2>
  </div>
  <svg class="abs" style="left:196px;top:3075px" width="52" height="44" viewBox="0 0 52 44"><path d="M6 4h26a4 4 0 0 1 4 4v14a4 4 0 0 1-4 4H16l-8 7v-7H6a4 4 0 0 1-4-4V8a4 4 0 0 1 4-4z" fill="none" stroke="#6ab43e" stroke-width="3"/><path d="M40 14h6a4 4 0 0 1 4 4v12a4 4 0 0 1-4 4h-2v6l-7-6H24" fill="none" stroke="#6ab43e" stroke-width="3"/></svg>
  <div class="abs" style="left:0;top:3128px;width:445px;text-align:center;font-size:16px;color:#333">Tel :</div>
  <div class="abs" style="left:0;top:3152px;width:445px;text-align:center;font-size:21px;color:#333">+44 1481 700 318</div>
  <svg class="abs" style="left:197px;top:3213px" width="50" height="38" viewBox="0 0 50 38"><rect x="2" y="2" width="46" height="34" fill="none" stroke="#6ab43e" stroke-width="3"/><path d="M2 2l23 19L48 2" fill="none" stroke="#6ab43e" stroke-width="3"/></svg>
  <div class="abs" style="left:0;top:3262px;width:445px;text-align:center;font-size:16px;color:#333">Email :</div>
  <div class="abs" style="left:0;top:3286px;width:445px;text-align:center;font-size:21px;color:#333">hello@brenlowestates.example</div>

  <div class="abs" style="left:407px;top:3079px;width:187px;height:44px;border:1px solid #bbb;background:#fff;font-size:14px;color:#888;padding:12px">Name</div>
  <div class="abs" style="left:604px;top:3079px;width:189px;height:44px;border:1px solid #bbb;background:#fff;font-size:14px;color:#888;padding:12px">Contact No.</div>
  <div class="abs" style="left:407px;top:3134px;width:386px;height:39px;border:1px solid #bbb;background:#fff;font-size:14px;color:#888;padding:10px 12px">E mail ID</div>
  <div class="abs" style="left:407px;top:3182px;width:386px;height:87px;border:1px solid #bbb;background:#fff;font-size:14px;color:#888;padding:10px 12px">Message...</div>
  <div class="btn" style="left:407px;top:3276px"><div class="btn-text">SUBMIT</div><div class="btn-icon"><svg width="24" height="24" viewBox="0 0 24 24"><path d="M21 3L3 11l8 2 2 8z" fill="#fff"/></svg></div></div>
</section>

<footer>
  <div class="abs" style="left:0;top:3365px;width:1200px;height:64px;background:var(--teal-dark)"></div>
  <div class="abs" style="left:78px;top:3378px;display:flex;gap:14px">
    <span style="width:40px;height:40px;border-radius:50%;background:var(--green);display:block"></span>
    <span style="width:40px;height:40px;border-radius:50%;background:var(--green);display:block"></span>
    <span style="width:40px;height:40px;border-radius:50%;background:var(--green);display:block"></span>
    <span style="width:40px;height:40px;border-radius:50%;background:var(--green);display:block"></span>
  </div>
  <div class="abs" style="right:80px;top:3386px;font-size:15px;color:var(--white)">© <span style="color:var(--green)">Brenlow Estates Ltd</span>. - 2016 All Right Reserved.</div>
</footer>

</body>
</html>
```